Coastline Premier Retreats Business Card Design

Design a business card for Coastline Premier Retreats. Look at the website for colors and reference. Card should have logo, name, title, office number, mobile number, email, URL and a tagline like, "Luxury Hotel & Resort Email Marketing" (This might change).

https://www.coastlinepremierretreats.example

The rest I will leave up to your imagination.

Contact Information for Business Card

Logo, name, title, office number, mobile number, email, URL and a tagline like, "Luxury Hotel & Resort Email Marketing" (This might change).

```html
<!DOCTYPE html>
<html lang="en">
<head>
<meta charset="utf-8">
<title>Coastline Premier Retreats – Business Card</title>
<link rel="stylesheet" href="https://fonts.googleapis.com/css2?family=Open+Sans:wght@400;600;700&display=swap">
<style>
  :root {
    --stage: #232323;
    --card-dark: #1f1f22;
    --card-dark-soft: #26262a;
    --brand-orange: #f37521;
    --ink-light: #ffffff;
    --ink-muted: #e6e6e6;
  }
  * { box-sizing: border-box; margin: 0; padding: 0; }
  html, body {
    width: 1200px; height: 780px; overflow: hidden;
    background: var(--stage);
    font-family: "Open Sans", Arial, sans-serif;
  }
  .stage {
    position: relative; width: 1200px; height: 780px;
    display: flex; align-items: center; justify-content: center; gap: 50px;
  }
  .card {
    position: relative; width: 525px; height: 300px; overflow: hidden;
    box-shadow: 0 14px 30px rgba(0,0,0,.45);
  }

  /* Front */
  .card--front { background: var(--card-dark); }
  .card__swoosh { position: absolute; inset: 0; }
  .brand-vertical {
    position: absolute; left: 18px; top: 150px;
    transform: translate(0, -50%) rotate(-90deg) translateY(0);
    transform-origin: left center;
  }
  .brand-vertical {
    left: 44px; top: 290px; transform: rotate(-90deg); transform-origin: left top;
    width: 280px; text-align: center;
    color: var(--ink-light); font-weight: 700; font-size: 19px; letter-spacing: .5px;
    white-space: nowrap;
  }
  .identity {
    position: absolute; right: 34px; top: 40px; text-align: right;
  }
  .identity__name { font-size: 29px; font-weight: 700; line-height: 1.1; color: var(--ink-light); }
  .identity__first { color: var(--brand-orange); }
  .identity__title { font-size: 13.5px; color: var(--ink-muted); margin-top: 4px; }
  .accent-bar {
    position: absolute; right: 0; top: 48px; width: 14px; height: 44px;
    background: var(--brand-orange);
  }
  .tagline {
    position: absolute; right: 34px; top: 130px; text-align: right;
    color: var(--brand-orange); font-size: 13.5px; line-height: 1.4;
  }
  .contact {
    position: absolute; right: 24px; bottom: 22px; list-style: none;
    color: var(--ink-muted); font-size: 12.5px; line-height: 1.55;
  }
  .contact__item { display: flex; align-items: center; justify-content: flex-end; gap: 8px; }
  .contact__icon { width: 13px; height: 13px; flex: none; }

  /* Back */
  .card--back {
    background: var(--brand-orange);
    display: flex; align-items: center; justify-content: center;
  }
  .brand-centered {
    color: var(--ink-light); font-weight: 700; font-size: 30px; letter-spacing: .5px;
    text-align: center;
  }
</style>
</head>
<body>
<main class="stage">
  <section class="card card--front" aria-label="Business card front">
    <svg class="card__swoosh" viewBox="0 0 525 300" aria-hidden="true">
      <path d="M115 300 C 140 170, 220 80, 330 70 L 525 70 L 525 300 Z" fill="var(--card-dark-soft)"/>
      <path d="M135 300 C 160 185, 235 100, 335 92 L 525 92 L 525 300 Z" fill="var(--card-dark)"/>
    </svg>

    <div class="brand-vertical">Coastline Premier Retreats</div>

    <div class="accent-bar"></div>
    <div class="identity">
      <p class="identity__name"><span class="identity__first">Lena</span> Harwick</p>
      <p class="identity__title">Managing Director</p>
    </div>

    <p class="tagline">Luxury Hotel &amp;<br>Resort Email Marketing</p>

    <ul class="contact">
      <li class="contact__item">(555) 014-2758
        <svg class="contact__icon" viewBox="0 0 16 16" aria-hidden="true"><path d="M3 1l3 3-1.5 2a9 9 0 0 0 5.5 5.5L12 10l3 3-2 2C7 15 1 9 1 3z" fill="var(--brand-orange)"/></svg>
      </li>
      <li class="contact__item">(555) 018-7777
        <svg class="contact__icon" viewBox="0 0 16 16" aria-hidden="true"><rect x="4" y="1" width="8" height="14" rx="1.5" fill="none" stroke="var(--brand-orange)" stroke-width="1.6"/></svg>
      </li>
      <li class="contact__item">www.coastlinepremierretreats.example
        <svg class="contact__icon" viewBox="0 0 16 16" aria-hidden="true"><circle cx="8" cy="8" r="6.5" fill="none" stroke="var(--brand-orange)" stroke-width="1.6"/><path d="M1.5 8h13M8 1.5c-3 3.5-3 9.5 0 13M8 1.5c3 3.5 3 9.5 0 13" fill="none" stroke="var(--brand-orange)" stroke-width="1.2"/></svg>
      </li>
      <li class="contact__item">info@coastlinepremierretreats.example
        <svg class="contact__icon" viewBox="0 0 16 16" aria-hidden="true"><rect x="1" y="3" width="14" height="10" rx="1" fill="var(--brand-orange)"/><path d="M1.5 3.5L8 9l6.5-5.5" fill="none" stroke="var(--card-dark)" stroke-width="1.4"/></svg>
      </li>
    </ul>
  </section>

  <section class="card card--back" aria-label="Business card back">
    <p class="brand-centered">Coastline Premier Retreats</p>
  </section>
</main>
</body>
</html>
```